Audio-Visual & Video Communications Business Requires a Cutting-edge Business Card Design

LinkVerra is a new Audio-Visual & Video Communications company in Cape Town, South Africa that is looking for a cutting-edge business card design. We sell these products to the Corporate, Education & Hospitality markets and will also host an Online Shop for companies and individuals to purchase our products online.

We are already using the following two colours in our logo and draft website. Please incorporate these colours into the design. Please note that our website is still in the design stage if you need to visit it. Green #a0ce4e & Dark Grey #333333.

Hi,

Please note that I have uploaded our logo in an .eps format.

Target Market(s)

Corporate Companies, Education Institutions & Hospitality Markets

Industry/Entity Type

Business

Requirements
Nice to have
• It would be great if you could incorporate the services that we offer.

1. Consultation & Design
2. Project Management
3. Supply & Installation
4. Onsite Support Personal
5. Online Shop

```html
<!DOCTYPE html>
<html lang="en">
<head>
<meta charset="utf-8">
<title>LinkVerra Business Card</title>
<link rel="stylesheet" href="https://fonts.googleapis.com/css2?family=Maven+Pro:wght@400;500;700&display=swap">
<style>
  :root {
    --green: #a0ce4e;
    --dark-grey: #333333;
    --card-grey: #5b5b5b;
    --text-grey: #4a4a4a;
    --paper: #ffffff;
    --backdrop: #e6e8ea;
  }
  * { margin: 0; padding: 0; box-sizing: border-box; }
  html, body {
    width: 1200px; height: 960px; overflow: hidden;
    background: var(--backdrop);
    font-family: "Maven Pro", sans-serif;
  }
  .canvas {
    position: relative; width: 1200px; height: 960px;
    display: flex; flex-direction: column; align-items: center; justify-content: center; gap: 40px;
  }
  .card {
    position: relative; width: 700px; height: 400px;
    box-shadow: 0 6px 20px rgba(0,0,0,0.15);
    overflow: hidden;
  }
  /* Front */
  .card-front { background: var(--paper); color: var(--text-grey); }
  .brand {
    position: absolute; top: 48px; right: 44px;
    display: flex; align-items: center; gap: 12px;
  }
  .brand-dot { width: 30px; height: 30px; border-radius: 50%; background: var(--green); }
  .brand-name { font-size: 44px; font-weight: 700; color: var(--green); letter-spacing: -0.5px; }
  .contact { position: absolute; left: 44px; top: 168px; }
  .contact-name { font-size: 34px; font-weight: 400; letter-spacing: 1px; color: var(--text-grey); }
  .contact-role { font-size: 19px; margin-top: 2px; margin-bottom: 18px; }
  .contact-line { font-size: 19px; line-height: 1.3; }
  .contact-line .label { color: var(--green); display: inline-block; width: 16px; }
  .contact-web { font-size: 20px; font-weight: 700; color: var(--green); margin-top: 14px; letter-spacing: 0.5px; }
  .contact-address { font-size: 19px; margin-top: 14px; letter-spacing: 0.3px; }
  /* Back */
  .card-back { background: var(--card-grey); color: var(--paper); }
  .back-mark {
    position: absolute; left: 60px; top: 60px;
    width: 280px; height: 280px; border-radius: 50%; background: var(--green);
  }
  .services {
    position: absolute; left: 400px; top: 140px; list-style: none;
    font-size: 16px; letter-spacing: 1px; line-height: 1.45;
  }
  .services li::before { content: "•"; color: var(--green); margin-right: 8px; }
</style>
</head>
<body>
<main class="canvas">
  <section class="card card-front" aria-label="Business card front">
    <div class="brand">
      <span class="brand-dot"></span>
      <span class="brand-name">LinkVerra</span>
    </div>
    <div class="contact">
      <p class="contact-name">DANA WHITLOCK</p>
      <p class="contact-role">Manager</p>
      <p class="contact-line"><span class="label">t</span> 555.014.2290</p>
      <p class="contact-line"><span class="label">e</span> support@linkverra.com</p>
      <p class="contact-web">www.linkverra.com</p>
      <p class="contact-address">PO Box 2210, Rondebosch, Cape Town, 7700, South Africa.</p>
    </div>
  </section>
  <section class="card card-back" aria-label="Business card back">
    <div class="back-mark"></div>
    <ul class="services">
      <li>Consultation &amp; Design</li>
      <li>Project Management</li>
      <li>Supply &amp; Installation</li>
      <li>Onsite Support Personal</li>
      <li>Online Shop</li>
    </ul>
  </section>
</main>
</body>
</html>
```